Digital Marketing Agency Landing Page

At VELIM, we offer a comprehensive solution for solar companies' client acquisition needs in the rapidly growing industry. We handle end-to-end client acquisition, meaning we manage the entire lifecycle of capturing new clients—from initial lead generation to delivering the ready-to-buy homeowner. Our expertise in targeted advertising, data analytics, and customer relationship management ensures that we not only find potential customers but also nurture them through tailored engagement strategies until they are ready to make a purchase. By entrusting us with your client acquisition process, solar companies can focus on what they do best—providing sustainable energy solutions—while we work behind the scenes to grow your customer base and increase your market share.

We need to restructure our website to make it more professional. We don't need any complex functionalities. We are looking for someone that is good in design and can build a visually aesthetic website following our brand image. We only need a landing page and a lead form in the end. I would like to have only one page, but a relatively big one where people scroll down. I would like to have a minimal and classy look. Something that is timeless and elegant.

Structure:

initial page
About us
How we operate
Get in touch

Target Market(s)

Solar Comapanies

Industry/Entity Type

Marketing solautions

Coding

Coded - Design and coding required

Number of Pages Required

1 page

Requirements
Nice to have
• Inspirations: https://www.qz.zu/ https://www.marchbeck.example/ https://www.tovanrid.example/ https://pruvo.example/

```html
<!DOCTYPE html>
<html lang="en">
<head>
<meta charset="utf-8">
<title>VELIM — Digital Marketing Agency</title>
<link href="https://fonts.googleapis.com/css2?family=Montserrat:wght@400;500;600;700&display=swap" rel="stylesheet">
<style>
  :root {
    --navy: #12202e;
    --cream: #ebe6da;
    --cream-line: #e4ded0;
    --white: #ffffff;
    --violet: #2a1650;
    --field-line: #9aa3ad;
  }
  * { box-sizing: border-box; margin: 0; padding: 0; }
  html, body { width: 669px; height: 1200px; overflow: hidden; }
  body {
    position: relative;
    background: var(--navy);
    font-family: "Montserrat", sans-serif;
    color: var(--white);
  }
  .abs { position: absolute; }

  /* Header */
  .site-header { left: 0; top: 0; width: 669px; height: 63px; background: var(--navy); }
  .brand {
    display: flex; align-items: center; gap: 8px;
    font-weight: 500; color: var(--cream-line); letter-spacing: 1px;
  }
  .brand-mark { width: 10px; height: 10px; background: var(--cream-line); flex: none; }
  .header-brand { left: 58px; top: 18px; height: 26px; font-size: 19px; }
  .call-icon {
    left: 431px; top: 19px; width: 29px; height: 29px; border-radius: 50%;
    background: var(--cream); border: 2px solid #8a8a86;
    display: flex; align-items: center; justify-content: center;
  }
  .call-text { left: 468px; top: 17px; font-size: 11px; font-weight: 600; line-height: 17px; color: var(--cream); }
  .menu-toggle { left: 597px; top: 25px; width: 12px; }
  .menu-toggle span { display: block; height: 2px; background: var(--white); margin-bottom: 2.5px; }

  /* Hero */
  .hero-frame-outer { left: 0; top: 63px; width: 655px; height: 334px; border: 3px solid var(--cream-line); }
  .hero-visual {
    left: 3px; top: 66px; width: 649px; height: 328px;
    background: linear-gradient(180deg, #1d1a4a 0%, var(--violet) 35%, #3a3a6a 70%, #7c8aa2 100%);
  }
  .hero-laptop {
    left: 33px; top: 168px; width: 290px; height: 220px;
    background: radial-gradient(ellipse at 50% 50%, rgba(150,175,210,0.55), rgba(90,110,150,0.25) 60%, rgba(0,0,0,0) 75%);
  }
  .hero-frame-inner { left: 18px; top: 80px; width: 655px; height: 335px; border: 3px solid var(--cream-line); border-right: none; }
  .hero-title { left: 0; top: 104px; width: 705px; text-align: center; font-size: 23px; font-weight: 600; color: var(--cream); letter-spacing: 0.3px; }
  .hero-lede { left: 148px; top: 136px; width: 374px; text-align: center; font-size: 8.6px; line-height: 13.5px; font-weight: 500; }

  .contact-card { left: 439px; top: 162px; width: 172px; height: 212px; background: var(--white); border-radius: 7px; overflow: hidden; }
  .contact-card h2 { height: 37px; background: var(--cream); color: var(--navy); font-size: 12px; font-weight: 500; text-align: center; line-height: 38px; letter-spacing: 0.2px; }
  .field { position: absolute; left: 15px; width: 141px; border-bottom: 1px solid var(--field-line); color: #2c3a48; font-size: 8px; padding-bottom: 6px; }
  .submit { position: absolute; left: 48px; top: 175px; width: 77px; height: 26px; background: var(--navy); color: var(--white); font-size: 10px; font-weight: 600; display: flex; align-items: center; justify-content: center; }

  /* About */
  .about-frame-back { left: 58px; top: 473px; width: 223px; height: 237px; border: 3px solid var(--cream-line); }
  .about-frame-front { left: 69px; top: 462px; width: 223px; height: 238px; border: 3px solid var(--cream-line); }
  .about-visual { left: 72px; top: 465px; width: 217px; height: 232px; background: linear-gradient(135deg, #5b4530, #8b6a47 45%, #a07e58 70%, #6d5239); }
  .about-title { left: 327px; top: 475px; font-size: 20px; font-weight: 600; color: var(--cream); }
  .about-copy { left: 325px; top: 508px; width: 280px; font-size: 8.3px; line-height: 13.5px; font-weight: 500; }
  .about-copy p + p { margin-top: 4.5px; }
  .btn-outline { left: 325px; top: 659px; width: 82px; height: 27px; border: 1px solid var(--white); font-size: 10px; font-weight: 600; display: flex; align-items: center; justify-content: center; }

  /* Services */
  .services { left: 0; top: 756px; width: 669px; height: 353px; background: var(--cream); }
  .services-title { left: 0; top: 800px; width: 669px; text-align: center; font-size: 21px; font-weight: 600; color: var(--navy); }
  .service-card { top: 851px; width: 159px; height: 199px; border: 3px solid var(--navy); border-radius: 3px; color: var(--navy); text-align: center; background: var(--cream); }
  .service-card.is-featured { background: var(--navy); color: var(--white); }
  .service-icon { position: absolute; left: 46px; top: 13px; width: 61px; height: 61px; border-radius: 50%; background: var(--navy); display: flex; align-items: center; justify-content: center; }
  .is-featured .service-icon { border: 1px solid var(--white); }
  .service-card h3 { position: absolute; left: 0; width: 100%; top: 88px; font-size: 11.2px; font-weight: 600; line-height: 15.5px; }
  .service-card p { position: absolute; left: 10px; width: 133px; font-size: 7.6px; line-height: 12.5px; font-weight: 500; }
  .service-card a { position: absolute; left: 0; width: 100%; top: 172px; font-size: 9.5px; font-weight: 600; color: inherit; text-decoration: underline; }

  /* Footer */
  .footer-brand { left: 123px; top: 1144px; height: 26px; font-size: 20px; }
  .footer-nav { left: 310px; top: 1146px; font-size: 10.3px; font-weight: 400; color: var(--white); word-spacing: 1px; }
  .footer-nav span { margin: 0 7px; }
</style>
</head>
<body>
  <header class="site-header abs"></header>
  <div class="brand header-brand abs"><span class="brand-mark"></span>VELIM</div>
  <div class="call-icon abs">
    <svg width="13" height="13" viewBox="0 0 24 24"><path fill="#12202e" d="M6.6 10.8c1.4 2.8 3.8 5.1 6.6 6.6l2.2-2.2c.3-.3.7-.4 1-.2 1.1.4 2.3.6 3.6.6.6 0 1 .4 1 1V20c0 .6-.4 1-1 1C10.6 21 3 13.4 3 4c0-.6.4-1 1-1h3.5c.6 0 1 .4 1 1 0 1.3.2 2.5.6 3.6.1.3 0 .7-.2 1z"/></svg>
  </div>
  <div class="call-text abs">Cal Us:<br>+1 555 014 2090</div>
  <div class="menu-toggle abs"><span></span><span></span><span></span></div>

  <section class="hero">
    <div class="hero-visual abs" role="img" aria-label="Laptop on a desk with floating marketing dashboards and charts"></div>
    <div class="hero-laptop abs" role="img" aria-label="Laptop with analytics panels"></div>
    <div class="hero-frame-outer abs"></div>
    <div class="hero-frame-inner abs"></div>
    <h1 class="hero-title abs">WELCOME TO VELIM</h1>
    <p class="hero-lede abs">Lorem ipsum dolor sit amet, consectetur adipiscing elit, sed do eiusmod tempor incididunt ut labore et dolore magna aliqua.</p>

    <form class="contact-card abs">
      <h2>CONTACT US</h2>
      <div class="field" style="top:55px">Name</div>
      <div class="field" style="top:85px">Email</div>
      <div class="field" style="top:115px">Phone</div>
      <div class="field" style="top:144px">Message</div>
      <div class="submit">SUBMIT</div>
    </form>
  </section>

  <section class="about">
    <div class="about-frame-back abs"></div>
    <div class="about-visual abs" role="img" aria-label="Team around a wooden table with digital marketing word cloud"></div>
    <div class="about-frame-front abs"></div>
    <h2 class="about-title abs">ABOUT TO VELIM</h2>
    <div class="about-copy abs">
      <p>Lorem ipsum dolor sit amet, consectetur adipiscing elit, sed do eiusmod tempor incididunt ut labore et dolore magna aliqua. Quis ipsum suspendisse ultrices gravida. Risus commodo viverra maecenas accumsan lacus vel facilisis.</p>
      <p>Sed ut perspiciatis unde omnis iste natus error sit voluptatem accusantium doloremque laudantium, totam rem aperiam, eaque ipsa quae ab illo inventore veritatis et quasi architecto beatae vitae dicta sunt explicabo. Nemo enim ipsam voluptatem quia voluptas sit aspernatur aut odit aut fugit, sed quia consequuntur magni dolores eos qui ratione voluptatem sequi nesciunt.</p>
    </div>
    <div class="btn-outline abs">READ MORE</div>
  </section>

  <section class="services abs"></section>
  <h2 class="services-title abs">OUR SERVICES</h2>

  <article class="service-card abs" style="left:76px">
    <div class="service-icon">
      <svg width="36" height="36" viewBox="0 0 36 36" fill="none" stroke="#fff" stroke-width="1.3"><path d="M6 24l14-10v16z"/><path d="M6 20v6h4"/><rect x="22" y="6" width="8" height="7"/><rect x="22" y="19" width="8" height="7"/><circle cx="16" cy="8" r="3"/><path d="M3 30h30"/></svg>
    </div>
    <h3>Advertising</h3>
    <p style="top:110px">Lorem ipsum dolor sit amet, adipiscing elit, sed do eiusmod tempor incididunt ut labore et dolore magna aliqua.</p>
    <a>Read More</a>
  </article>

  <article class="service-card is-featured abs" style="left:255px">
    <div class="service-icon">
      <svg width="38" height="38" viewBox="0 0 38 38" fill="none" stroke="#fff" stroke-width="1.3"><rect x="4" y="12" width="30" height="18"/><path d="M15 30l-2 5h12l-2-5"/><path d="M9 12V7M13 12V4M17 12V6M21 12V8"/><circle cx="28" cy="8" r="4"/><path d="M7 25l6-5 6 3 6-6 7 3"/></svg>
    </div>
    <h3>Data Analytics</h3>
    <p style="top:110px">Lorem ipsum dolor sit amet, adipiscing elit, sed do eiusmod tempor incididunt ut labore et dolore magna aliqua.</p>
    <a>Read More</a>
  </article>

  <article class="service-card abs" style="left:435px">
    <div class="service-icon">
      <svg width="38" height="38" viewBox="0 0 38 38" fill="none" stroke="#fff" stroke-width="1.3"><rect x="7" y="16" width="24" height="14"/><path d="M15 34h8M19 30v4"/><circle cx="19" cy="23" r="3"/><circle cx="19" cy="5" r="2.5"/><path d="M15 12a4 4 0 018 0"/><circle cx="6" cy="10" r="2.5"/><path d="M2 17a4 4 0 018 0"/><circle cx="32" cy="10" r="2.5"/><path d="M28 17a4 4 0 018 0"/></svg>
    </div>
    <h3>Customer Relationship<br>Management</h3>
    <p style="top:126px">Lorem ipsum dolor sit amet, adipiscing elit, sed do eiusmod tempor et dolore magna aliqua.</p>
    <a>Read More</a>
  </article>

  <footer>
    <div class="brand footer-brand abs"><span class="brand-mark"></span>VELIM</div>
    <nav class="footer-nav abs">Home<span>|</span>About Us<span>|</span>Our Services<span>|</span>Contact Us</nav>
  </footer>
</body>
</html>
```